Tidewell-Network Theme For Forums!

We are looking for a theme for our forums. The forums are ran off Invision Power Boards. We have a basic theme on there now but we want more our own feel. If possible have some longboarding accept incorporated in the theme. We want the theme to have some red in it to match our logo. Tidewell-network.com

Target Market(s)

Skatingboarding & Longboarding

Coding

Coded - Design and coding required

Number of Pages Required

1 page

Colors
f04a50

```html
<!DOCTYPE html>
<html lang="en">
<head>
<meta charset="utf-8">
<title>Tidewell-Network</title>
<link rel="stylesheet" href="https://fonts.googleapis.com/css2?family=Roboto:wght@400;500;700&family=Roboto+Condensed:wght@700&display=swap">
<style>
:root{
  --red:#e8343e;
  --red-dark:#c5121c;
  --ink:#2a2a2a;
  --dark:#1e1e1e;
  --panel-dark:#2e2e2e;
  --pink:#f3d3d5;
  --page:#f1efee;
  --line:#e3e0df;
  --text:#333;
  --muted:#555;
}
*{box-sizing:border-box;margin:0;padding:0}
html,body{width:1002px;height:1200px;overflow:hidden}
body{background:var(--page);font-family:"Roboto",sans-serif;color:var(--text);position:relative}
.topbar{position:absolute;left:0;top:0;width:1002px;height:97px;background:var(--dark);border-top:3px solid var(--red-dark)}
.brand{position:absolute;left:47px;top:26px;display:flex;align-items:center;gap:8px;color:#fff;font-family:"Roboto Condensed",sans-serif;font-weight:700;font-size:24px;letter-spacing:.5px}
.brand-mark{width:16px;height:16px;background:var(--red)}
.search{position:absolute;left:470px;top:22px;width:254px;height:22px;border-bottom:1px solid #ccc;color:#ddd;font-size:11px;padding:4px 6px}
.search svg{position:absolute;right:6px;top:6px}
.user-panel{position:absolute;right:0;top:0;width:240px;height:56px;background:var(--red-dark)}
.avatar-lg{position:absolute;left:8px;top:7px;width:52px;height:43px;background:linear-gradient(#d9e2ea,#7b8796);border:1px solid #fff}
.user-select{position:absolute;left:68px;top:8px;width:92px;height:15px;background:var(--red);color:#fff;font-size:9px;padding:2px 5px}
.count-select{position:absolute;left:166px;top:8px;width:26px;height:15px;background:var(--red);color:#fff;font-size:9px;padding:2px 5px}
.user-select::after,.count-select::after{content:"";position:absolute;right:5px;top:6px;border:3px solid transparent;border-top-color:#fff}
.user-links{position:absolute;left:70px;top:39px;color:#fff;font-size:9px}
.user-links a{color:#fff;text-decoration:underline}
.nav{position:absolute;left:385px;top:70px;display:flex;gap:22px;color:#fff;font-size:10.5px;font-weight:500}
.crumbs{position:absolute;left:0;top:97px;width:1002px;height:36px;background:var(--pink);font-size:13px;font-weight:500;color:var(--ink)}
.crumbs .home{position:absolute;left:45px;top:11px}
.crumbs .sep{position:absolute;left:106px;top:0}
.crumbs .here{position:absolute;left:127px;top:11px}
.crumbs .all{position:absolute;left:744px;top:11px;display:flex;gap:5px;align-items:center}
.social{position:absolute;left:858px;top:7px;display:flex;gap:3px}
.social span{width:22px;height:22px;border-radius:2px}
.page-title{position:absolute;left:45px;top:180px;font-size:24px;font-weight:700;color:#111}
.main{position:absolute;left:46px;top:226px;width:634px}
.section{margin-bottom:42px}
.section-head{height:37px;background:var(--red);color:#fff;font-size:17px;font-weight:500;display:flex;align-items:center;padding-left:12px;position:relative;margin-bottom:5px}
.section-head .toggle{position:absolute;right:0;top:0;width:43px;height:37px;background:var(--red-dark);display:flex;align-items:center;justify-content:center}
.topic{display:flex;gap:5px;height:59px;margin-bottom:5px}
.topic-icon{width:74px;background:#fff;border:1px solid var(--line);display:flex;align-items:center;justify-content:center}
.topic-body{flex:1;background:#fff;border:1px solid var(--line);position:relative}
.topic-name{position:absolute;left:13px;top:12px;font-size:13px;font-weight:500;color:#444}
.topic-desc{position:absolute;left:13px;top:34px;font-size:10.5px;color:#444}
.topic-stats{position:absolute;right:226px;top:13px;text-align:right;font-size:10.5px;line-height:19.5px;color:#555}
.topic-avatar{position:absolute;left:339px;top:8px;width:42px;height:42px;border:1px solid #ccc}
.topic-last{position:absolute;left:393px;top:13px;font-size:10.5px;line-height:19.5px;color:#555}
.meta{display:flex;gap:7px;align-items:center}
.meta span{display:inline-flex;align-items:center;gap:2px}
.side{position:absolute;left:714px;width:241px;background:#fff;border:1px solid var(--line)}
.side-head{height:38px;background:var(--panel-dark);color:#fff;font-size:15px;font-weight:700;display:flex;align-items:center;padding-left:14px;position:relative}
.side-head.red{background:var(--red-dark)}
.side-head svg{position:absolute;right:14px;top:15px}
.side-item{display:flex;gap:12px;padding:14px 16px 0 14px}
.side-item+.side-item{border-top:1px solid var(--line);margin:0 16px 0 14px;padding:14px 0 0}
.thumb{width:48px;height:48px;flex:none;border:1px solid #ccc}
.side-text{font-size:10.5px;line-height:17px;color:#555}
.side-text .meta{margin-top:4px}
.tabs{height:38px;background:var(--pink);display:flex;justify-content:center;gap:0;padding-top:12px}
.tabs span{width:86px;height:26px;font-size:13px;text-align:center;padding-top:5px;color:#333}
.tabs .on{background:#fff}
.video{margin:19px 12px 16px;height:127px;background:linear-gradient(135deg,#9aa4ae,#4b5056 60%,#8a8f93);position:relative}
.play{position:absolute;left:50%;top:50%;width:30px;height:30px;margin:-15px 0 0 -15px;border-radius:50%;background:#fff;opacity:.9}
.play::after{content:"";position:absolute;left:12px;top:9px;border:6px solid transparent;border-left:9px solid var(--red)}
.btns{display:flex;gap:12px;padding:18px 0 0 15px}
.btn{height:28px;font-size:12px;font-weight:500;display:flex;align-items:center;gap:5px;padding:0 12px}
.btn.fill{background:var(--red-dark);color:#fff}
.btn.line{border:2px solid var(--red);color:var(--red)}
.folder{background:#fff;display:flex;align-items:center;justify-content:center}
.footer{position:absolute;left:0;top:1128px;width:1002px;height:72px;background:var(--panel-dark);color:#fff;font-size:12px;text-align:center;padding-top:27px}
.ic{flex:none}
</style>
</head>
<body>
<header class="topbar">
  <div class="brand"><span class="brand-mark"></span>TIDEWELL-NETWORK</div>
  <div class="search">Search Here...
    <svg width="10" height="10" viewBox="0 0 10 10"><circle cx="4" cy="4" r="3" fill="none" stroke="#fff" stroke-width="1.6"/><path d="M6.3 6.3 9 9" stroke="#fff" stroke-width="1.8"/></svg>
  </div>
  <div class="user-panel">
    <div class="avatar-lg" role="img" aria-label="Member profile photo"></div>
    <div class="user-select">Rook</div>
    <div class="count-select">8</div>
    <div class="user-links"><a>Sign Out</a> &nbsp;| &nbsp;<a>Help</a></div>
  </div>
  <nav class="nav"><span>PORTAL</span><span>WHAT'S NEW?</span><span>FORUM</span><span>TOPLIST</span><span>PLAY</span><span>RULES</span><span>FAQ</span><span>COMMUNITY</span><span>FORUM ACTIONS</span></nav>
</header>

<div class="crumbs">
  <span class="home">HOME</span>
  <svg class="sep" width="14" height="36" viewBox="0 0 14 36"><path d="M1 0 12 18 1 36" fill="none" stroke="#e59aa0" stroke-width="1"/></svg>
  <span class="here">ACTIVITY</span>
  <span class="all"><svg width="13" height="10" viewBox="0 0 13 10"><path d="M0 1h4l1 1h6v2H3L0 10Z" fill="#e8343e"/><path d="M3 4h10l-3 6H0Z" fill="#e8343e"/></svg>ALL ACTIVITY</span>
  <div class="social"><span style="background:#3b5998"></span><span style="background:#1da1f2"></span><span style="background:#d6336c"></span><span style="background:#d91c1c"></span></div>
</div>

<h1 class="page-title">TIDEWELL-NETWORK</h1>

<svg width="0" height="0" style="position:absolute">
  <defs>
    <symbol id="board" viewBox="0 0 60 60"><g transform="rotate(-45 30 30)"><rect x="4" y="23" width="52" height="14" rx="7"/><circle cx="46" cy="27" r="1.6" fill="#fff"/><circle cx="46" cy="33" r="1.6" fill="#fff"/><circle cx="14" cy="27" r="1.6" fill="#fff"/><circle cx="14" cy="33" r="1.6" fill="#fff"/></g></symbol>
    <symbol id="user" viewBox="0 0 10 10"><circle cx="5" cy="3" r="2.5"/><path d="M0 10c0-4 10-4 10 0Z"/></symbol>
    <symbol id="cal" viewBox="0 0 10 10"><rect x="0" y="1.5" width="10" height="8.5" rx="1"/><rect x="1.5" y="4" width="7" height="4.5" fill="#fff"/></symbol>
    <symbol id="chat" viewBox="0 0 12 10"><ellipse cx="6" cy="4.5" rx="5.3" ry="3.8" fill="none" stroke="currentColor" stroke-width="1.4"/><path d="M2 7 1 10 5 8Z"/></symbol>
    <symbol id="up" viewBox="0 0 14 8"><path d="M1 7 7 1l6 6" fill="none" stroke="#fff" stroke-width="2"/></symbol>
  </defs>
</svg>

<main class="main">
  <section class="section">
    <div class="section-head">IMPORTANT TOPICS<span class="toggle"><svg width="14" height="8"><use href="#up"/></svg></span></div>
    <div class="topic"><div class="topic-icon"><svg width="50" height="50" fill="#3a3a3a"><use href="#board"/></svg></div><div class="topic-body"><div class="topic-name">The Forum Name</div><div class="topic-desc">This is the forum description.feel free to take!</div><div class="topic-stats">10 Replies<br>7,114 Views</div><div class="topic-avatar" role="img" aria-label="Member avatar" style="background:linear-gradient(#e8612c,#4d5964)"></div><div class="topic-last">Duis aute irure dolor in<div class="meta"><span><svg width="9" height="9" fill="#e8343e"><use href="#user"/></svg>Kael</span><span><svg width="9" height="9" fill="#e8343e"><use href="#cal"/></svg>31 May 2018 at 3pm.</span></div></div></div></div>
    <div class="topic"><div class="topic-icon"><svg width="50" height="50" fill="#e8343e"><use href="#board"/></svg></div><div class="topic-body"><div class="topic-name">The Forum Name</div><div class="topic-desc">This is the forum description.feel free to take!</div><div class="topic-stats">10 Replies<br>7,114 Views</div><div class="topic-avatar" role="img" aria-label="Member avatar" style="background:linear-gradient(#c9a36a,#2b2220)"></div><div class="topic-last">Duis aute irure dolor in<div class="meta"><span><svg width="9" height="9" fill="#e8343e"><use href="#user"/></svg>Kael</span><span><svg width="9" height="9" fill="#e8343e"><use href="#cal"/></svg>31 May 2018 at 3pm.</span></div></div></div></div>
    <div class="topic"><div class="topic-icon"><svg width="50" height="50" fill="#3a3a3a"><use href="#board"/></svg></div><div class="topic-body"><div class="topic-name">The Forum Name</div><div class="topic-desc">This is the forum description.feel free to take!</div><div class="topic-stats">10 Replies<br>7,114 Views</div><div class="topic-avatar" role="img" aria-label="Member avatar" style="background:linear-gradient(#b7c8de,#d95a5a)"></div><div class="topic-last">Duis aute irure dolor in<div class="meta"><span><svg width="9" height="9" fill="#e8343e"><use href="#user"/></svg>Kael</span><span><svg width="9" height="9" fill="#e8343e"><use href="#cal"/></svg>31 May 2018 at 3pm.</span></div></div></div></div>
  </section>

  <section class="section">
    <div class="section-head">FORM TOPICS<span class="toggle"><svg width="14" height="8"><use href="#up"/></svg></span></div>
    <div class="topic"><div class="topic-icon"><svg width="50" height="50" fill="#3a3a3a"><use href="#board"/></svg></div><div class="topic-body"><div class="topic-name">The Forum Name</div><div class="topic-desc">This is the forum description.feel free to take!</div><div class="topic-stats">10 Replies<br>7,114 Views</div><div class="topic-avatar" role="img" aria-label="Member avatar" style="background:linear-gradient(#d8d8d8,#3d3029)"></div><div class="topic-last">Duis aute irure dolor in<div class="meta"><span><svg width="9" height="9" fill="#e8343e"><use href="#user"/></svg>Kael</span><span><svg width="9" height="9" fill="#e8343e"><use href="#cal"/></svg>31 May 2018 at 3pm.</span></div></div></div></div>
    <div class="topic"><div class="topic-icon"><svg width="50" height="50" fill="#3a3a3a"><use href="#board"/></svg></div><div class="topic-body"><div class="topic-name">The Forum Name</div><div class="topic-desc">This is the forum description.feel free to take!</div><div class="topic-stats">10 Replies<br>7,114 Views</div><div class="topic-avatar" role="img" aria-label="Member avatar" style="background:linear-gradient(#5c8a3a,#4a2a1e)"></div><div class="topic-last">Duis aute irure dolor in<div class="meta"><span><svg width="9" height="9" fill="#e8343e"><use href="#user"/></svg>Kael</span><span><svg width="9" height="9" fill="#e8343e"><use href="#cal"/></svg>31 May 2018 at 3pm.</span></div></div></div></div>
    <div class="topic"><div class="topic-icon"><svg width="50" height="50" fill="#e8343e"><use href="#board"/></svg></div><div class="topic-body"><div class="topic-name">The Forum Name</div><div class="topic-desc">This is the forum description.feel free to take!</div><div class="topic-stats">10 Replies<br>7,114 Views</div><div class="topic-avatar" role="img" aria-label="Member avatar" style="background:linear-gradient(#7fb2d6,#c9a183)"></div><div class="topic-last">Duis aute irure dolor in<div class="meta"><span><svg width="9" height="9" fill="#e8343e"><use href="#user"/></svg>Kael</span><span><svg width="9" height="9" fill="#e8343e"><use href="#cal"/></svg>31 May 2018 at 3pm.</span></div></div></div></div>
    <div class="topic"><div class="topic-icon"><svg width="50" height="50" fill="#3a3a3a"><use href="#board"/></svg></div><div class="topic-body"><div class="topic-name">The Forum Name</div><div class="topic-desc">This is the forum description.feel free to take!</div><div class="topic-stats">10 Replies<br>7,114 Views</div><div class="topic-avatar" role="img" aria-label="Member avatar" style="background:linear-gradient(#6aa1c9,#c0392b)"></div><div class="topic-last">Duis aute irure dolor in<div class="meta"><span><svg width="9" height="9" fill="#e8343e"><use href="#user"/></svg>Kael</span><span><svg width="9" height="9" fill="#e8343e"><use href="#cal"/></svg>31 May 2018 at 3pm.</span></div></div></div></div>
  </section>

  <section class="section">
    <div class="section-head">FORM TOPICS<span class="toggle"><svg width="14" height="8"><use href="#up"/></svg></span></div>
    <div class="topic"><div class="topic-icon"><svg width="50" height="50" fill="#3a3a3a"><use href="#board"/></svg></div><div class="topic-body"><div class="topic-name">The Forum Name</div><div class="topic-desc">This is the forum description.feel free to take!</div><div class="topic-stats">10 Replies<br>7,114 Views</div><div class="topic-avatar" role="img" aria-label="Member avatar" style="background:linear-gradient(#e2e2e2,#9e2a2a)"></div><div class="topic-last">Duis aute irure dolor in<div class="meta"><span><svg width="9" height="9" fill="#e8343e"><use href="#user"/></svg>Kael</span><span><svg width="9" height="9" fill="#e8343e"><use href="#cal"/></svg>31 May 2018 at 3pm.</span></div></div></div></div>
    <div class="topic"><div class="topic-icon"><svg width="50" height="50" fill="#3a3a3a"><use href="#board"/></svg></div><div class="topic-body"><div class="topic-name">The Forum Name</div><div class="topic-desc">This is the forum description.feel free to take!</div><div class="topic-stats">10 Replies<br>7,114 Views</div><div class="topic-avatar" role="img" aria-label="Member avatar" style="background:linear-gradient(#cfcfcf,#2f3a48)"></div><div class="topic-last">Duis aute irure dolor in<div class="meta"><span><svg width="9" height="9" fill="#e8343e"><use href="#user"/></svg>Kael</span><span><svg width="9" height="9" fill="#e8343e"><use href="#cal"/></svg>31 May 2018 at 3pm.</span></div></div></div></div>
    <div class="topic"><div class="topic-icon"><svg width="50" height="50" fill="#e8343e"><use href="#board"/></svg></div><div class="topic-body"><div class="topic-name">The Forum Name</div><div class="topic-desc">This is the forum description.feel free to take!</div><div class="topic-stats">10 Replies<br>7,114 Views</div><div class="topic-avatar" role="img" aria-label="Member avatar" style="background:linear-gradient(#8fa37a,#2d2d2d)"></div><div class="topic-last">Duis aute irure dolor in<div class="meta"><span><svg width="9" height="9" fill="#e8343e"><use href="#user"/></svg>Kael</span><span><svg width="9" height="9" fill="#e8343e"><use href="#cal"/></svg>31 May 2018 at 3pm.</span></div></div></div></div>
  </section>
</main>

<aside class="side" style="top:226px;height:271px">
  <div class="side-head">Recent Status Updates<svg width="10" height="6" viewBox="0 0 10 6"><path d="M1 1l4 4 4-4" fill="none" stroke="#fff" stroke-width="1.6"/></svg></div>
  <div class="side-item"><div class="thumb" role="img" aria-label="Member photo" style="background:linear-gradient(#cfd8c8,#5b6b4d)"></div><div class="side-text">Duis aute irutere dolor in sint non occaecat cupidatat<div class="meta"><span><svg width="9" height="9" fill="#e8343e"><use href="#user"/></svg>Kael</span><span><svg width="9" height="9" fill="#e8343e"><use href="#cal"/></svg>31 May 2018</span><span style="color:#e8343e"><svg width="11" height="9" fill="#e8343e"><use href="#chat"/></svg><b style="color:#555;font-weight:400">30</b></span></div></div></div>
  <div class="side-item"><div class="thumb" role="img" aria-label="Member photo" style="background:linear-gradient(#9bb27d,#5c6e80)"></div><div class="side-text">Duis aute irutere dolor in sint non occaecat cupidatat<div class="meta"><span><svg width="9" height="9" fill="#e8343e"><use href="#user"/></svg>Kael</span><span><svg width="9" height="9" fill="#e8343e"><use href="#cal"/></svg>31 May 2018</span><span style="color:#e8343e"><svg width="11" height="9" fill="#e8343e"><use href="#chat"/></svg><b style="color:#555;font-weight:400">30</b></span></div></div></div>
  <div class="side-item"><div class="thumb" role="img" aria-label="Member photo" style="background:linear-gradient(#e0dcd6,#4a3a30)"></div><div class="side-text">Duis aute irutere dolor in sint non occaecat cupidatat<div class="meta"><span><svg width="9" height="9" fill="#e8343e"><use href="#user"/></svg>Kael</span><span><svg width="9" height="9" fill="#e8343e"><use href="#cal"/></svg>31 May 2018</span><span style="color:#e8343e"><svg width="11" height="9" fill="#e8343e"><use href="#chat"/></svg><b style="color:#555;font-weight:400">30</b></span></div></div></div>
</aside>

<aside class="side" style="top:532px;height:238px">
  <div class="side-head red">Latest Video Post<svg width="10" height="6" viewBox="0 0 10 6"><path d="M1 1l4 4 4-4" fill="none" stroke="#fff" stroke-width="1.6"/></svg></div>
  <div class="tabs"><span class="on">Form</span><span>Topic</span></div>
  <div class="video" role="img" aria-label="Video still of a skater riding a board"><span class="play"></span></div>
</aside>

<aside class="side" style="top:807px;height:255px">
  <div class="side-head">Latest File<svg width="10" height="6" viewBox="0 0 10 6"><path d="M1 1l4 4 4-4" fill="none" stroke="#fff" stroke-width="1.6"/></svg></div>
  <div class="side-item"><div class="thumb folder"><svg width="38" height="32" viewBox="0 0 38 32"><path d="M2 4h12l3 3h19v22H2Z" fill="#e8961c"/><path d="M5 11h32l-3 18H2Z" fill="#f6b63a"/></svg></div><div class="side-text">Duis aute irutere dolor in sint non occaecat cupidatat<div class="meta"><span><svg width="9" height="9" fill="#e8343e"><use href="#user"/></svg>Kael</span><span><svg width="9" height="9" fill="#e8343e"><use href="#cal"/></svg>31 May 2018</span><span style="color:#e8343e"><svg width="11" height="9" fill="#e8343e"><use href="#chat"/></svg><b style="color:#555;font-weight:400">30</b></span></div></div></div>
  <div class="side-item"><div class="thumb folder"><svg width="38" height="32" viewBox="0 0 38 32"><path d="M2 4h12l3 3h19v22H2Z" fill="#e8961c"/><path d="M5 11h32l-3 18H2Z" fill="#f6b63a"/></svg></div><div class="side-text">Duis aute irutere dolor in sint non occaecat cupidatat<div class="meta"><span><svg width="9" height="9" fill="#e8343e"><use href="#user"/></svg>Kael</span><span><svg width="9" height="9" fill="#e8343e"><use href="#cal"/></svg>31 May 2018</span><span style="color:#e8343e"><svg width="11" height="9" fill="#e8343e"><use href="#chat"/></svg><b style="color:#555;font-weight:400">30</b></span></div></div></div>
  <div class="btns">
    <span class="btn fill">View All <svg width="10" height="10" viewBox="0 0 10 10"><circle cx="5" cy="5" r="5" fill="#fff"/><path d="M4 2.5 6.5 5 4 7.5" fill="none" stroke="#c5121c" stroke-width="1.5"/></svg></span>
    <span class="btn line">Upload File</span>
  </div>
</aside>

<footer class="footer">Copyrights © 2018 Tidewell-Network. &nbsp;All Rights Reserved.</footer>
</body>
</html>
```